Laser, Botox, fillers,

I need a few designs for Botox, dermal fillers, laser IPL, Hair removal, hyperpigmentation removal, scar reduction resurface, PRP Hair restoration and PRP joint injections. Office number for appointments is 646-318-2054

Requirements
Must have
• Use the pictures below for dermal fillers need to show how dermal fillers improve

```html
<!DOCTYPE html>
<html lang="en">
<head>
<meta charset="utf-8">
<title>Halvorsen NP Walk In Clinic – Hair Removal Poster</title>
<link href="https://fonts.googleapis.com/css2?family=Cinzel:wght@400;600;700&display=swap" rel="stylesheet">
<style>
  :root {
    --stage-top: #e4e4e4;
    --stage-bottom: #c9c9c9;
    --paper: #efefef;
    --paper-white: #ffffff;
    --brand-red: #b01318;
    --brand-red-soft: #ecc9cb;
    --charcoal: #3b3b3d;
    --ink: #2f2f31;
    --photo-wall: #c9b098;
    --photo-skin: #e4cdbb;
    --photo-towel: #f5f2ee;
    --photo-glove: #aebbe0;
  }
  * { margin: 0; padding: 0; box-sizing: border-box; }
  html, body {
    width: 1200px;
    height: 2666px;
    overflow: hidden;
  }
  body {
    background: linear-gradient(180deg, var(--stage-top), var(--stage-bottom));
    font-family: "Cinzel", serif;
  }
  .poster {
    position: absolute;
    left: 80px;
    top: 599px;
    width: 1040px;
    height: 1468px;
    box-shadow: 0 10px 30px rgba(0,0,0,0.18);
  }
  .poster svg { display: block; width: 100%; height: 100%; }
  .brand-small { font-family: "Cinzel", serif; font-weight: 400; fill: var(--brand-red); }
  .brand-large { font-family: "Cinzel", serif; font-weight: 400; fill: var(--ink); }
  .badge-label { font-family: "Cinzel", serif; font-weight: 400; fill: var(--paper-white); }
  .cta-heading { font-family: "Cinzel", serif; font-weight: 700; fill: var(--ink); }
  .contact-text { font-family: "Cinzel", serif; font-weight: 400; fill: var(--paper-white); }
</style>
</head>
<body>
  <div class="poster">
    <svg viewBox="0 0 620 875" xmlns="http://www.w3.org/2000/svg">
      <defs>
        <clipPath id="photo-clip"><circle cx="310" cy="438" r="243"/></clipPath>
        <linearGradient id="photo-tone" x1="0" y1="0" x2="1" y2="1">
          <stop offset="0%" stop-color="var(--photo-wall)"/>
          <stop offset="35%" stop-color="var(--photo-skin)"/>
          <stop offset="65%" stop-color="var(--photo-towel)"/>
          <stop offset="100%" stop-color="var(--photo-glove)"/>
        </linearGradient>
      </defs>

      <!-- paper and white swoosh -->
      <rect class="paper" width="620" height="875" fill="var(--paper)"/>
      <circle class="swoosh" cx="330" cy="440" r="345" fill="var(--paper-white)"/>

      <!-- corner bands -->
      <path class="corner-red" d="M373 0 H620 V121 Q540 30 373 0 Z" fill="var(--brand-red)"/>
      <path class="corner-dark" d="M0 753 Q70 840 245 875 H0 Z" fill="var(--charcoal)"/>

      <!-- brand lockup -->
      <circle class="brand-mark" cx="193" cy="91" r="57" fill="var(--charcoal)"/>
      <line class="brand-divider" x1="267" y1="38" x2="267" y2="146" stroke="var(--brand-red)" stroke-width="2"/>
      <text class="brand-small" x="287" y="66" font-size="22">Halvorsen NP</text>
      <text class="brand-large" x="287" y="101" font-size="34">Walk In</text>
      <text class="brand-large" x="287" y="132" font-size="34">Clinic, PC</text>

      <!-- photo frame -->
      <circle class="photo-ring" cx="310" cy="436" r="260" fill="none" stroke="var(--brand-red)" stroke-width="1.2"/>
      <g clip-path="url(#photo-clip)">
        <rect class="photo" x="60" y="190" width="500" height="500" fill="url(#photo-tone)" role="img" aria-label="Photo of a client receiving a laser hair removal treatment on the jaw"/>
      </g>

      <!-- service badge -->
      <circle class="badge-halo" cx="148" cy="618" r="87" fill="var(--brand-red-soft)"/>
      <circle class="badge" cx="148" cy="618" r="78" fill="var(--brand-red)"/>
      <text class="badge-label" x="148" y="605" font-size="30" text-anchor="middle">Hair</text>
      <text class="badge-label" x="148" y="639" font-size="25" text-anchor="middle">REMOVAL</text>

      <!-- call to action -->
      <text class="cta-heading" x="307" y="758" font-size="22" text-anchor="middle">FOR APPOINTMENTS</text>
      <rect class="contact-pill" x="83" y="776" width="459" height="42" rx="21" fill="var(--brand-red)"/>
      <g class="icon-phone">
        <circle cx="105" cy="797" r="12" fill="var(--paper-white)"/>
        <path d="M99 790 q-2 2 0 6 q3 6 9 9 q4 2 6 0 l1-2 -4-3 -2 2 q-4-2-6-6 l2-2 -3-4 z" fill="var(--brand-red)"/>
      </g>
      <text class="contact-text" x="125" y="805" font-size="20">646-318-2054</text>
      <line x1="265" y1="786" x2="265" y2="808" stroke="var(--paper-white)" stroke-width="1.5"/>
      <g class="icon-globe" fill="none" stroke="var(--brand-red)" stroke-width="1.2">
        <circle cx="288" cy="797" r="12" fill="var(--paper-white)" stroke="none"/>
        <circle cx="288" cy="797" r="7.5"/>
        <ellipse cx="288" cy="797" rx="3.2" ry="7.5"/>
        <line x1="280.5" y1="797" x2="295.5" y2="797"/>
      </g>
      <text class="contact-text" x="309" y="804" font-size="17">WWW.HALVORSENNP.COM</text>
    </svg>
  </div>
</body>
</html>
```